Birchwell Agency Condominium mail merge

We need a marketing proposal letter design to do a mail merge to potential e customers. We included our logo and an example of my miserable attempt to create a template. We are looking for a modern and attractive proposal template. Here is our website https://www.birchwellagency.example to be used for any additional information needed about us and our services.

Target Market(s)

New prospects

Industry/Entity Type

Insurance Agency

Requirements
Must have
• My project must have a modern professional look with merge fields similar to the file uploaded with this project.
Nice to have
• it would like have a condominium and a car icon graphic depicting there is additional discounts for both quotes bundled.
Should not have
• My project should not have any other logos or company name

```html
<!DOCTYPE html>
<html lang="en">
<head>
<meta charset="utf-8">
<title>Birchwell Agency Letterhead</title>
<link rel="stylesheet" href="https://fonts.googleapis.com/css2?family=Source+Sans+3:wght@400;600;700&family=Arimo:wght@700&display=swap">
<style>
  :root {
    --green: #3db54a;
    --orange: #f58220;
    --ink: #454545;
    --paper: #ffffff;
    --backdrop: #e4e4e4;
  }
  html, body {
    margin: 0;
    width: 1059px;
    height: 1200px;
    overflow: hidden;
    background: var(--backdrop);
  }
  .letter {
    position: absolute;
    left: 121px;
    top: 24px;
    width: 816px;
    height: 1152px;
    background: var(--paper);
    font-family: "Source Sans 3", sans-serif;
    color: var(--ink);
    overflow: hidden;
  }
  .brand-name {
    position: absolute;
    left: 66px;
    top: 72px;
    margin: 0;
    font-weight: 700;
    font-size: 34px;
    letter-spacing: -0.5px;
    color: var(--green);
  }
  .contact {
    position: absolute;
    left: 570px;
    top: 56px;
    font-size: 13px;
    line-height: 17px;
  }
  .contact-name { color: var(--green); font-weight: 700; font-size: 13.5px; }
  .contact-role { color: var(--orange); }
  .contact-line { display: flex; align-items: center; gap: 6px; }
  .contact-line svg { width: 11px; height: 11px; fill: var(--green); }
  .salutation {
    position: absolute;
    left: 79px;
    top: 298px;
    margin: 0;
    font-family: "Arimo", sans-serif;
    font-weight: 700;
    font-size: 17px;
    color: var(--ink);
  }
  .body-copy {
    position: absolute;
    left: 80px;
    top: 344px;
    width: 665px;
  }
  .body-copy p {
    margin: 0 0 21px;
    font-size: 16px;
    line-height: 21.4px;
    letter-spacing: -0.2px;
  }
  .body-copy .line {
    display: block;
    white-space: nowrap;
    text-align: justify;
    text-align-last: justify;
  }
  .body-copy .line.last { text-align-last: left; }
  .signature {
    position: absolute;
    left: 80px;
    top: 748px;
    width: 156px;
    height: 78px;
    background: linear-gradient(90deg, #f2f2f2, #e8e8e8);
  }
  .footer-rule {
    position: absolute;
    left: 0;
    bottom: 82px;
    width: 816px;
    height: 4px;
    background: var(--orange);
  }
  .footer-band {
    position: absolute;
    left: 0;
    bottom: 0;
    width: 816px;
    height: 78px;
    background: var(--green);
  }
  .footer-info {
    position: absolute;
    right: 68px;
    bottom: 16px;
    text-align: right;
    color: #fff;
    font-size: 11.5px;
    line-height: 17px;
  }
  .footer-info strong { font-weight: 700; }
  .footer-info .web { font-size: 13px; }
</style>
</head>
<body>
<main class="letter">
  <header>
    <h1 class="brand-name">Birchwell Agency</h1>
    <div class="contact">
      <div class="contact-name">Graham Teller</div>
      <div class="contact-role">Agency Principal</div>
      <div class="contact-line">
        <svg viewBox="0 0 24 24" aria-hidden="true"><path d="M6.6 10.8a15.1 15.1 0 0 0 6.6 6.6l2.2-2.2a1 1 0 0 1 1-.25 11.4 11.4 0 0 0 3.6.57 1 1 0 0 1 1 1V20a1 1 0 0 1-1 1A17 17 0 0 1 3 4a1 1 0 0 1 1-1h3.5a1 1 0 0 1 1 1c0 1.250.2 2.45.57 3.57a1 1 0 0 1-.25 1z"/></svg>
        <span>555-014-2290</span>
      </div>
      <div class="contact-line">
        <svg viewBox="0 0 24 24" aria-hidden="true"><path d="M2 5h20v14H2z M2 5l10 8 10-8" stroke="#fff" stroke-width="1.5"/></svg>
        <span>graham@birchwellagency.example</span>
      </div>
    </div>
  </header>

  <h2 class="salutation">Dear Mr. Hale,</h2>

  <section class="body-copy">
    <p>
      <span class="line">Lorem Ipsum is simply dummy text of the printing and typesetting industry. Lorem Ipsum</span>
      <span class="line">has been the industry's standard dummy text ever since the 1500s, when an unknown</span>
      <span class="line">printer took a galley of type and scrambled it to make a type specimen book. It has survived</span>
      <span class="line">not only five centuries, but also the leap into electronic typesetting, remaining essentially</span>
      <span class="line last">unchanged.</span>
    </p>
    <p>
      <span class="line">The standard chunk of Lorem Ipsum used since the 1500s is reproduced below for those</span>
      <span class="line">interested. Sections 1.10.32 and 1.10.33 from "de Finibus Bonorum et Malorum" by Tullian</span>
      <span class="line">are also reproduced in their exact original form, accompanied by English versions from the</span>
      <span class="line last">1914 translation by H. Ramsdell</span>
    </p>
    <p>
      <span class="line">Lorem Ipsum is simply dummy text of the printing and typesetting industry. Lorem Ipsum</span>
      <span class="line">has been the industry's standard dummy text ever since the 1500s, when an unknown</span>
      <span class="line">printer took a galley of type and scrambled it to make a type specimen book. It has survived</span>
      <span class="line">not only five centuries, but also the leap into electronic typesetting, remaining essentially</span>
      <span class="line last">unchanged. It was popularised in the</span>
    </p>
  </section>

  <div class="signature" role="img" aria-label="Handwritten signature of the sender"></div>

  <footer>
    <div class="footer-rule"></div>
    <div class="footer-band"></div>
    <div class="footer-info">
      <div><strong>Birchwell Agency, Inc</strong></div>
      <div>742 Linden Avenue Ste. 210 Harbor Springs, FL 32001</div>
      <div class="web">www.birchwellagency.example</div>
    </div>
  </footer>
</main>
</body>
</html>
```